Quillmarsh Property Solutions need a business card design

Hello guys. We would need a business card design asap please.
We are a start up property investment business based in London UK specialised in buying, selling, managing and letting properties and helping distressed property owners.
The name of our Business is Quillmarsh, the logo symbolises the four fundamental elements of the world (earth, air, fire and water) and so it stands for strength, stability, longevity.
We would like the business card to communicate professionalism and reliability. Many many thanks indeed for your work.

Details:

1.) Rosalind Updike
Property Investor
Mobile: +44(0)7700123456
Email: rosalind.quillmarsh@mailbox-example.com

2.) Dominic Updike
Property Investor
Mobile: +44(0)7700987654
Email: dominic.quillmarsh@mailbox-example.com

```html
<!DOCTYPE html>
<html lang="en">
<head>
<meta charset="utf-8">
<title>Quillmarsh Property Solutions – Business Card</title>
<link rel="stylesheet" href="https://fonts.googleapis.com/css2?family=Open+Sans:wght@400;600;700;800&display=swap">
<style>
  :root {
    --canvas-bg: #e9e7e3;
    --card-white: #ffffff;
    --ink-dark: #1c1c1c;
    --ink-grey: #5d5f63;
    --brand-red: #c8283a;
    --brand-blue: #3a66b8;
    --brand-green: #0f6a37;
    --divider: #c9c9c9;
    --back-blue-light: #5b94e6;
    --back-blue-dark: #2e62c4;
  }
  * { margin: 0; padding: 0; box-sizing: border-box; }
  html, body {
    width: 1200px; height: 720px; overflow: hidden;
    background: var(--canvas-bg);
    font-family: "Open Sans", Arial, sans-serif;
  }
  .canvas {
    position: relative; width: 1200px; height: 720px;
    display: flex; align-items: center; justify-content: center; gap: 50px;
  }
  .card {
    position: relative; width: 540px; height: 316px;
    overflow: hidden; border-radius: 3px;
    box-shadow: 0 6px 18px rgba(0,0,0,0.18);
  }
  .card-front { background: var(--card-white); }
  .card-bands { position: absolute; inset: 0; }

  .wordmark {
    position: absolute; left: 0; width: 540px; text-align: center;
    top: 96px;
  }
  .wordmark-name {
    font-weight: 800; font-size: 30px; letter-spacing: 1px;
    color: var(--ink-dark); line-height: 1;
  }
  .wordmark-tagline {
    margin-top: 6px; font-weight: 700; font-size: 9px;
    letter-spacing: 1.5px; color: var(--ink-dark);
  }

  .holder {
    position: absolute; right: 290px; top: 196px; text-align: right;
  }
  .holder-name { font-weight: 600; font-size: 18px; color: var(--brand-red); line-height: 1.2; }
  .holder-role { font-size: 14px; color: var(--brand-blue); line-height: 1.3; }

  .divider {
    position: absolute; left: 262px; top: 186px; width: 1px; height: 62px;
    background: var(--divider);
  }
  .contact { position: absolute; left: 274px; top: 188px; list-style: none; }
  .contact-item {
    display: flex; align-items: center; gap: 6px;
    font-size: 12px; color: var(--ink-grey); line-height: 26px;
  }
  .contact-icon { width: 12px; height: 12px; flex: none; }

  .card-back {
    background: radial-gradient(circle at 45% 40%, var(--back-blue-light), var(--back-blue-dark) 75%);
    display: flex; align-items: center; justify-content: center;
  }
  .back-wordmark {
    font-weight: 800; font-size: 40px; letter-spacing: 2px; color: var(--card-white);
  }
</style>
</head>
<body>
<main class="canvas">

  <section class="card card-front" aria-label="Business card front">
    <svg class="card-bands" width="540" height="316" viewBox="0 0 540 316" aria-hidden="true">
      <polygon points="0,298 246,298 240,316 0,316" fill="var(--brand-red)"/>
      <polygon points="262,270 540,270 540,316 252,316" fill="var(--brand-green)"/>
    </svg>

    <div class="wordmark">
      <div class="wordmark-name">QUILLMARSH</div>
      <div class="wordmark-tagline">PROPERTY SOLUTIONS</div>
    </div>

    <div class="holder">
      <p class="holder-name">Dominic Updike</p>
      <p class="holder-role">Property Investor</p>
    </div>

    <div class="divider"></div>

    <ul class="contact">
      <li class="contact-item">
        <svg class="contact-icon" viewBox="0 0 12 12" aria-hidden="true">
          <rect x="3" y="0.5" width="6" height="11" rx="1.2" fill="var(--brand-blue)"/>
          <rect x="4" y="2" width="4" height="6" fill="#fff"/>
        </svg>
        +44(0)7700987654
      </li>
      <li class="contact-item">
        <svg class="contact-icon" viewBox="0 0 12 12" aria-hidden="true">
          <circle cx="6" cy="6" r="6" fill="var(--brand-blue)"/>
          <rect x="3" y="4" width="6" height="4" fill="#fff"/>
          <polyline points="3,4 6,6.3 9,4" fill="none" stroke="var(--brand-blue)" stroke-width="0.8"/>
        </svg>
        dominic.quillmarsh@mailbox-example.com
      </li>
    </ul>
  </section>

  <section class="card card-back" aria-label="Business card back">
    <div class="back-wordmark">QUILLMARSH</div>
  </section>

</main>
</body>
</html>
```